Landscape design build company door flyer

I would like this flyer to convey a high-level of professionalism for a company that is excellent with communication with their clients as well as a company that does incredible installations

Went on vacation/holiday

```html
<!DOCTYPE html>
<html lang="en">
<head>
<meta charset="utf-8">
<title>Cedarstone Builders – Door Flyer</title>
<link href="https://fonts.googleapis.com/css2?family=Montserrat:wght@400;500;600;700;800&display=swap" rel="stylesheet">
<style>
:root{
  --navy:#0c2a3e;
  --gold:#f5b400;
  --white:#ffffff;
  --panel:#f1f1f1;
  --bg:#e6e6e6;
  --text-light:#eef2f5;
}
*{margin:0;padding:0;box-sizing:border-box}
html,body{width:1200px;height:1029px;overflow:hidden;background:var(--bg);font-family:"Montserrat",sans-serif}
.stage{position:relative;width:1200px;height:1029px}
.flyer{position:absolute;left:212px;top:15px;width:1250px;height:1608px;transform:scale(0.6206);transform-origin:0 0;background:var(--white);overflow:hidden}
.hero{position:absolute;left:0;top:80px;width:1250px;height:1050px;background:var(--navy)}
.brand-frame{position:absolute;left:0;top:0}
.brand-name{position:absolute;left:468px;top:155px;width:300px;text-align:center;font-weight:700;font-size:23px;letter-spacing:.5px;color:var(--navy)}
.headline{position:absolute;left:0;top:268px;width:1250px;text-align:center;font-weight:800;font-size:71px;line-height:77px;color:var(--white);letter-spacing:-.5px}
.headline .accent{color:var(--gold)}
.about{position:absolute;left:97px;top:560px;width:434px;color:var(--text-light)}
.about h2{font-weight:600;font-size:29px;margin-bottom:10px;color:var(--white)}
.about p{font-size:19.6px;line-height:23.9px;text-align:justify;margin-bottom:24px;font-weight:500}
.photo{position:absolute}
.services{position:absolute;left:0;top:1130px;width:1250px;height:278px;background:linear-gradient(90deg,#fff 0%,#fff 42%,#c9ced2 75%,#5b6b77 92%,var(--navy) 100%)}
.services h2{position:absolute;left:97px;top:18px;font-weight:700;font-size:29px;color:var(--navy)}
.service{position:absolute;display:flex;align-items:center;gap:14px;font-weight:700;font-size:18.5px;color:#1d2b36;letter-spacing:.3px}
.service svg{width:44px;height:44px;flex:none}
.badge{position:absolute;left:967px;top:57px}
.contact{position:absolute;left:0;top:1408px;width:1250px;height:188px;background:var(--navy)}
.contact h2{position:absolute;left:98px;top:26px;font-weight:600;font-size:26px;color:var(--white)}
.phone{position:absolute;left:94px;top:64px;display:flex;align-items:center;gap:20px;font-weight:600;font-size:68px;color:var(--gold);letter-spacing:-1px}
.email{position:absolute;right:48px;top:80px;font-size:26px;font-weight:400;color:var(--text-light);letter-spacing:.5px}
</style>
</head>
<body>
<div class="stage">
  <div class="flyer">
    <section class="hero"></section>

    <svg class="brand-frame" width="1250" height="290" viewBox="0 0 1250 290">
      <polygon points="367,0 468,0 468,220 367,80" fill="#f1f1f1"/>
      <polygon points="768,0 868,0 868,80 768,220" fill="#f1f1f1"/>
      <polygon points="367,80 468,220 468,0" fill="#f1f1f1"/>
      <rect x="468" y="0" width="300" height="220" fill="#fff"/>
      <polygon points="365,80 468,220 468,0 365,0" fill="#f1f1f1"/>
      <rect x="468" y="0" width="300" height="220" fill="#fff"/>
      <polygon points="768,0 870,0 870,80 768,220" fill="#f1f1f1"/>
      <line x1="468" y1="220" x2="468" y2="275" stroke="#000" stroke-width="1.5"/>
      <line x1="768" y1="220" x2="768" y2="275" stroke="#000" stroke-width="1.5"/>
    </svg>
    <div class="brand-name">CEDARSTONE BUILDERS</div>

    <h1 class="headline">LET’S CREATE<br><span class="accent">YOUR DREAM OUTDOOR</span><br>LIVING SPACE!</h1>

    <div class="about">
      <h2>ABOUT US</h2>
      <p>Discover the endless possibilities for your outdoor space with The Cedarstone Builders Team. Our team of skilled artisans is dedicated to turning your outdoor space into a breathtaking oasis that you’ll love coming home to. Whether it’s a cozy patio for intimate gatherings, a sprawling deck to host memorable parties, or a custom paver driveway that adds instant curb appeal, our high-quality craftsmanship ensures stunning results that exceed your expectations.</p>
      <p>From concept to completion, we take pride in every detail, using the finest materials to withstand Seattle’s climate while adding timeless elegance to your property. Embrace the Pacific Northwest lifestyle and create cherished moments with family and friends in a captivating outdoor haven.</p>
    </div>

    <div class="photo" role="img" aria-label="Evening paver patio with firepit, seating walls and pool" style="left:593px;top:572px;width:209px;height:209px;background:linear-gradient(160deg,#3d4a4c,#6b6c6a 55%,#4a3a2c)"></div>
    <div class="photo" role="img" aria-label="Aerial view of a pool framed by grey decking" style="left:820px;top:572px;width:335px;height:209px;background:linear-gradient(135deg,#9aa7ab,#cfd5d6 45%,#3fb5b0 60%,#d9dddd)"></div>
    <div class="photo" role="img" aria-label="Stone garage with wooden doors and paver driveway" style="left:593px;top:797px;width:209px;height:146px;background:linear-gradient(180deg,#8e8678,#7a3d22 45%,#9a8a7a)"></div>
    <div class="photo" role="img" aria-label="Stone retaining wall with steps" style="left:593px;top:958px;width:209px;height:146px;background:linear-gradient(180deg,#5a4a38,#6d6d6b 35%,#8a8a88)"></div>
    <div class="photo" role="img" aria-label="Aerial view of a home with new paver driveway and walkways" style="left:820px;top:797px;width:335px;height:307px;background:linear-gradient(160deg,#3e5a34,#7c8288 40%,#5a5e60 70%,#5a3a28)"></div>

    <section class="services">
      <h2>OUR SERVICES</h2>
      <div class="service" style="left:100px;top:80px">
        <svg viewBox="0 0 44 44"><path d="M4 42V16L22 4l18 12v26" fill="none" stroke="#1d2b36" stroke-width="3"/><rect x="13" y="22" width="18" height="14" fill="none" stroke="#1d2b36" stroke-width="2.5"/><line x1="13" y1="29" x2="31" y2="29" stroke="#1d2b36" stroke-width="2"/></svg>Paver Patios</div>
      <div class="service" style="left:100px;top:144px">
        <svg viewBox="0 0 44 44"><path d="M4 42V16L22 4l18 12v26" fill="none" stroke="#1d2b36" stroke-width="3"/><polygon points="10,36 16,26 28,26 34,36" fill="#1d2b36"/></svg>Paver Driveways</div>
      <div class="service" style="left:100px;top:210px">
        <svg viewBox="0 0 44 44"><path d="M4 42V16L22 4l18 12v26" fill="none" stroke="#1d2b36" stroke-width="3"/><path d="M12 20h12v5h6v5h-5v6h-7v-6h-6z" fill="#1d2b36"/></svg>Retaining Walls</div>
      <div class="service" style="left:366px;top:80px">
        <svg viewBox="0 0 44 44"><path d="M4 42V16L22 4l18 12v26" fill="none" stroke="#1d2b36" stroke-width="3"/><path d="M17 16v12M25 16v12M17 20h8M17 25h8M11 31q3-2 6 0t6 0 6 0 6 0M11 36q3-2 6 0t6 0 6 0 6 0" fill="none" stroke="#1d2b36" stroke-width="2"/></svg>Pools</div>
      <div class="service" style="left:366px;top:144px">
        <svg viewBox="0 0 44 44"><path d="M4 42V16L22 4l18 12v26" fill="none" stroke="#1d2b36" stroke-width="3"/><rect x="11" y="21" width="22" height="4" fill="#1d2b36"/><path d="M13 25v11M18 25v11M22 25v11M26 25v11M31 25v11M11 32h22" stroke="#1d2b36" stroke-width="2"/></svg>Decks &amp; Railings</div>
      <div class="service" style="left:366px;top:210px">
        <svg viewBox="0 0 44 44"><path d="M4 42V16L22 4l18 12v26" fill="none" stroke="#1d2b36" stroke-width="3"/><path d="M11 26l11-9 11 9v10H11z" fill="none" stroke="#1d2b36" stroke-width="2.5"/><path d="M22 36c-4 0-5-4-2-7 0 2 2 2 2 0 2 2 4 4 0 7z" fill="#1d2b36"/></svg>Firepits &amp; Fireplaces</div>
      <div class="service" style="left:641px;top:80px">
        <svg viewBox="0 0 44 44"><path d="M4 42V16L22 4l18 12v26" fill="none" stroke="#1d2b36" stroke-width="3"/><path d="M18 20h8l-1 10h-6z" fill="none" stroke="#1d2b36" stroke-width="2.2"/><line x1="22" y1="30" x2="22" y2="37" stroke="#1d2b36" stroke-width="2.2"/><line x1="22" y1="15" x2="22" y2="20" stroke="#1d2b36" stroke-width="2.2"/></svg>Outdoor Lighting</div>
      <div class="service" style="left:641px;top:144px">
        <svg viewBox="0 0 44 44"><path d="M4 42V16L22 4l18 12v26" fill="none" stroke="#1d2b36" stroke-width="3"/><circle cx="22" cy="28" r="8" fill="none" stroke="#1d2b36" stroke-width="2"/><path d="M22 23v10M17 28h10" stroke="#1d2b36" stroke-width="2"/></svg>And More...</div>

      <svg class="badge" width="186" height="186" viewBox="0 0 186 186" role="img" aria-label="Twenty years of experience seal">
        <defs><radialGradient id="seal-gold" cx="40%" cy="35%" r="70%"><stop offset="0" stop-color="#fbe27a"/><stop offset="1" stop-color="#b8860b"/></radialGradient></defs>
        <circle cx="93" cy="93" r="91" fill="url(#seal-gold)"/>
        <circle cx="93" cy="93" r="58" fill="#2a2a2a"/>
        <circle cx="93" cy="93" r="58" fill="none" stroke="#e6c34a" stroke-width="3"/>
      </svg>
    </section>

    <section class="contact">
      <h2>CONTACT US TODAY</h2>
      <div class="phone">
        <svg width="62" height="62" viewBox="0 0 24 24"><path d="M6.6 10.8a15.1 15.1 0 0 0 6.6 6.6l2.2-2.2c.3-.3.7-.4 1-.2 1.1.4 2.3.6 3.6.6.6 0 1 .4 1 1V20c0 .6-.4 1-1 1A17 17 0 0 1 3 4c0-.6.4-1 1-1h3.5c.6 0 1 .4 1 1 0 1.3.2 2.5.6 3.6.1.3 0 .7-.2 1z" fill="#f5b400"/><path d="M14 3a7 7 0 0 1 7 7M14 6.5a3.5 3.5 0 0 1 3.5 3.5" fill="none" stroke="#f5b400" stroke-width="1.8" stroke-linecap="round"/></svg>
        <span>[206]-555-0142</span>
      </div>
      <div class="email">info@cedarstonebuilders.com</div>
    </section>
  </div>
</div>
</body>
</html>
```